QuillVane needs a dashboard page designed

Redesign the dashboard shown in the provided images.

There are two images:
- dashboard.png
- dashboard-expanded.png

NOTE: The vocabulary navigation on the left will be a very long list of words 100s, so keep that in mind when you're designing both the vocab navigation and the expanded vocab popup.

In the dashboard.png picture, there needs to be a progress chart showing the word progress like the following: review 1(show it as completed) -> review 2(show the user they are here) -> review 3(unvisited) -> review 4(unvisited)

The do-not-design-this-page.png image is for your reference only. It is not to be designed. Use it to understand the overall look and feel of the website to help you create the best dashboard page possible.
Updates

Need extra days to review

Industry/Entity Type

Education English learning

Number of Pages Required

1 page

Requirements
Must have
• The main navigation and main header cannot change between pages. See the do-not-design page for the main navigateion and header.
Should not have
• Do not add a person profile. We will not have images of our users. Keep the icons in the main navigation as they are.

```html
<!DOCTYPE html>
<html lang="en">
<head>
<meta charset="utf-8">
<title>QuillVane – Vocabulary Dashboard</title>
<link rel="stylesheet" href="https://fonts.googleapis.com/css2?family=Poppins:wght@400;500;600;700&display=swap">
<style>
:root{
  --backdrop:#fbeed6;
  --night:#1c1328;
  --night-soft:#2a2040;
  --night-line:#3a3052;
  --white:#ffffff;
  --ink:#1d1a24;
  --muted:#7b778a;
  --yellow:#f4b41a;
  --purple:#6e56cf;
  --lavender:#efecfb;
  --lavender-line:#cfc6f2;
  --peach:#fdeee4;
  --peach-line:#f5c3a4;
  --orange:#e8713c;
  --sky:#e6f4fa;
  --sky-line:#a9d8ea;
  --cream:#fdf3d6;
  --cream-line:#f2d98b;
  --band-long:#eeeafb;
  --band-work:#eaf7ea;
  --band-short:#fdebe1;
  --band-forgot:#e4f2fa;
  --red:#e5484d;
  --chip:#ececf1;
}
*{box-sizing:border-box;margin:0;padding:0}
html,body{width:836px;height:1200px;overflow:hidden}
body{background:var(--backdrop);font-family:"Poppins",sans-serif;color:var(--ink);position:relative}

.screen{position:absolute;left:107px;width:621px;background:var(--white);box-shadow:0 4px 18px rgba(60,40,20,.18);overflow:hidden}
.screen--overview{top:147px;height:438px}
.screen--picker{top:612px;height:441px}

.topbar{position:absolute;left:0;top:0;right:0;height:18px;background:var(--night);display:flex;align-items:center;justify-content:space-between;padding:0 8px 0 10px}
.brand{color:var(--white);font-size:7px;font-weight:600}
.topbar__tools{display:flex;gap:4px;align-items:center}
.tool{width:7px;height:7px;border:1px solid #cfcad9;border-radius:50%}
.account{width:12px;height:12px;border-radius:50%;background:var(--yellow);margin-left:2px}

.rail{position:absolute;left:0;top:18px;bottom:0;width:27px;background:var(--night);display:flex;flex-direction:column;align-items:center;padding-top:8px;gap:10px}
.rail__item{display:flex;flex-direction:column;align-items:center;gap:2px;color:#cfcad9;font-size:3.6px;text-align:center;line-height:1.2}
.rail__item--active{color:var(--yellow)}
.rail__item svg{width:8px;height:8px}

.vocab-nav{position:absolute;left:27px;top:18px;bottom:0;width:102px;background:var(--night-soft);padding:8px 7px;color:var(--white)}
.vocab-nav__select{height:13px;border-bottom:1px solid var(--night-line);display:flex;justify-content:space-between;align-items:center;font-size:5px;margin-bottom:8px}
.vocab-group{margin-bottom:8px}
.vocab-group__title{display:flex;justify-content:space-between;align-items:center;font-size:5.6px;font-weight:600;margin-bottom:2px}
.info{width:6px;height:6px;border:0.8px solid currentColor;border-radius:50%;font-size:4px;display:inline-flex;align-items:center;justify-content:center}
.vocab-group ul{list-style:none}
.vocab-group li{font-size:4.6px;color:#cfcad9;line-height:7.4px}
.vocab-group li.current{color:var(--yellow);font-weight:600}

.main{position:absolute;left:129px;top:18px;right:0;bottom:0}

.reviews{position:absolute;left:10px;top:19px;display:flex;gap:8px}
.review{width:112px;height:44px;border:1px solid;border-radius:4px;padding:7px 8px;position:relative}
.review--done{background:var(--lavender);border-color:var(--lavender-line)}
.review--here{background:var(--peach);border-color:var(--peach-line)}
.review--next{background:var(--sky);border-color:var(--sky-line)}
.review--last{background:var(--cream);border-color:var(--cream-line)}
.review__label{font-size:4.6px;font-weight:500;color:var(--muted);letter-spacing:.3px}
.review__status{font-size:5.4px;font-weight:500;margin-top:2px}
.review--done .review__status{color:var(--purple)}
.review--here .review__status{color:var(--orange)}
.review--next .review__status{color:#4d8fae}
.review--last .review__status{color:#c89a1a}
.review__bar{position:absolute;left:8px;bottom:8px;width:68px;height:2.4px;border-radius:2px;background:rgba(0,0,0,.08)}
.review__bar span{display:block;height:100%;border-radius:2px}
.review--done .review__bar span{width:100%;background:var(--purple)}
.review--here .review__bar span{width:45%;background:var(--orange)}
.review__mark{position:absolute;right:9px;top:11px;width:18px;height:18px;border-radius:50%;background:var(--white);display:flex;align-items:center;justify-content:center}
.review--done .review__mark{border:1px solid var(--lavender-line)}
.review__mark svg{width:10px;height:10px}

.word{position:absolute;left:16px;top:84px;width:336px}
.word__title{font-size:11px;font-weight:700;display:flex;align-items:center;gap:3px}
.word__title svg{width:9px;height:9px}
.word__text{font-size:4.7px;line-height:7.2px;color:#3b3846;margin-top:3px}

.exercise{position:absolute;left:364px;top:82px;width:116px;height:72px;background:var(--cream);border-radius:4px;overflow:hidden;text-align:center}
.exercise__art{height:44px;margin:4px 24px 0;border-radius:4px;background:linear-gradient(160deg,#f7c74a,#e9a62a 55%,#3a2e45)}
.exercise__cta{font-size:4.6px;font-weight:700;line-height:6px;margin-top:5px;letter-spacing:.2px}

.curve-card{position:absolute;left:16px;top:160px;width:464px;height:185px;background:var(--white);border-radius:5px;box-shadow:0 2px 10px rgba(40,30,70,.14);padding:10px 12px}
.curve-card__title{font-size:8.6px;font-weight:600}
.curve-card svg{position:absolute;left:12px;top:28px}

.analysis{position:absolute;left:20px;top:354px;width:460px}
.analysis__title{font-size:9.6px;font-weight:700}
.analysis__text{font-size:4.7px;line-height:7.2px;color:#3b3846;margin-top:3px}

.scrim{position:absolute;inset:0;background:rgba(28,19,40,.58)}
.picker{position:absolute;left:138px;top:111px;width:357px;height:162px;background:var(--white);border-radius:10px;padding:12px 14px;box-shadow:0 8px 30px rgba(0,0,0,.3)}
.picker__select{width:125px;height:12px;border:1px solid #dcdae3;border-radius:3px;font-size:4.8px;display:flex;justify-content:space-between;align-items:center;padding:0 5px}
.picker__close{position:absolute;right:14px;top:13px;width:10px;height:10px;border-radius:50%;background:var(--red);color:var(--white);font-size:6px;display:flex;align-items:center;justify-content:center}
.picker__group{margin-top:11px}
.picker__group h3{font-size:5.6px;font-weight:600;display:flex;align-items:center;gap:4px;color:var(--ink)}
.picker__group h3 .info{color:var(--muted)}
.picker__words{display:flex;flex-wrap:wrap;gap:4px;margin-top:4px}
.picker__plain{font-size:4.6px;margin-top:3px;padding-bottom:5px;border-bottom:1px solid #ecebf0}
.chip{font-size:4.4px;background:var(--chip);border-radius:2px;padding:2px 6px}
</style>
</head>
<body>

<!-- Overview screen -->
<section class="screen screen--overview">
  <header class="topbar">
    <span class="brand">QuillVane ▾</span>
    <div class="topbar__tools"><span class="tool"></span><span class="tool"></span><span class="tool"></span><span class="account"></span></div>
  </header>
  <nav class="rail">
    <div class="rail__item rail__item--active"><svg viewBox="0 0 10 10"><path d="M1 5 5 1l4 4v4H6V6H4v3H1z" fill="currentColor"/></svg>QuillVane</div>
    <div class="rail__item"><svg viewBox="0 0 10 10"><path d="M5 1a3 3 0 0 1 3 3c0 2-3 5-3 5S2 6 2 4a3 3 0 0 1 3-3z" fill="currentColor"/></svg>Daily<br>English</div>
    <div class="rail__item"><svg viewBox="0 0 10 10"><path d="M1 9h8V4L5 1 1 4zM3 5h1v3H3zm3 0h1v3H6z" fill="currentColor"/></svg>Business</div>
  </nav>
  <aside class="vocab-nav">
    <div class="vocab-nav__select"><span>All</span><span>▾</span></div>
    <div class="vocab-group">
      <div class="vocab-group__title">Short-Term Memory <span class="info">?</span></div>
      <ul><li class="current">GRAB</li></ul>
    </div>
    <div class="vocab-group">
      <div class="vocab-group__title">Working Memory <span class="info">?</span></div>
      <ul><li>Cool Down</li><li>Cram</li><li>Go For</li><li>Go To</li><li>In The Mood For</li><li>Sip</li><li>Soothing</li><li>Stick With</li><li>Throw In/Throw On</li></ul>
    </div>
    <div class="vocab-group">
      <div class="vocab-group__title">Long-Term Memory <span class="info">?</span></div>
      <ul><li>Give It A Try</li></ul>
    </div>
  </aside>
  <main class="main">
    <div class="reviews">
      <div class="review review--done"><div class="review__label">REVIEW 1</div><div class="review__status">Completed</div><div class="review__bar"><span></span></div><div class="review__mark"><svg viewBox="0 0 10 10"><circle cx="5" cy="5" r="5" fill="#6e56cf"/><path d="M3 5.2 4.4 6.5 7 3.8" stroke="#fff" stroke-width="1.1" fill="none"/></svg></div></div>
      <div class="review review--here"><div class="review__label">REVIEW 2</div><div class="review__status">You are here</div><div class="review__bar"><span></span></div><div class="review__mark"><svg viewBox="0 0 10 10"><circle cx="5" cy="3.4" r="1.8" fill="#e8713c"/><path d="M1.8 9a3.2 3.2 0 0 1 6.4 0z" fill="#e8713c"/></svg></div></div>
      <div class="review review--next"><div class="review__label">REVIEW 3</div><div class="review__status">Unvisited</div><div class="review__mark"></div></div>
      <div class="review review--last"><div class="review__label">REVIEW 4</div><div class="review__status">Unvisited</div><div class="review__mark"></div></div>
    </div>
    <article class="word">
      <h1 class="word__title">Grab <svg viewBox="0 0 10 10"><path d="M5 .6 6.3 3.6l3.2.3-2.4 2.1.7 3.2L5 7.5 2.2 9.2l.7-3.2L.5 3.9l3.2-.3z" fill="#f4b41a"/></svg></h1>
      <p class="word__text">The word "<b>grab</b>" is most commonly used as a <b>verb</b>, meaning <b>to take something quickly or suddenly</b>. Imagine you're running late for school. You don't have time for breakfast, so you quickly <b>grab</b> an apple from the kitchen and rush out the door. As you reach the bus stop, your friend waves &amp; says, "Hey! Let's <b>grab</b> a coffee after class." Later, when you sit down, your phone starts ringing. You <b>grab</b> it from your bag and answer.</p>
    </article>
    <div class="exercise">
      <div class="exercise__art" role="img" aria-label="Illustration of a learner studying with a laptop"></div>
      <div class="exercise__cta">START VOCABULARY<br>REVIEW EXERCISE 3</div>
    </div>
    <section class="curve-card">
      <h2 class="curve-card__title">Learning Curve Graph</h2>
      <svg width="440" height="155" viewBox="0 0 440 155" font-family="Poppins, sans-serif">
        <rect x="0" y="3" width="440" height="26" fill="#eeeafb"/>
        <rect x="0" y="29" width="440" height="59" fill="#eaf7ea"/>
        <rect x="0" y="88" width="440" height="16" fill="#fdebe1"/>
        <rect x="0" y="104" width="440" height="20" fill="#e4f2fa"/>
        <g font-size="4.4" fill="#8a86a0"><text x="4" y="13">Long-Term Memory</text><text x="4" y="51">Working Memory</text><text x="4" y="96">Short-Term Memory</text><text x="4" y="113">Forgotten Memory</text></g>
        <path d="M207 30 A94 94 0 0 1 301 124" stroke="#9a96ab" stroke-width="0.7" fill="none"/>
        <path d="M158 93 Q175 80 207 78" stroke="#c9c6d4" stroke-width="0.6" fill="none"/>
        <rect x="156" y="94" width="3.5" height="30" fill="#1d1a24"/>
        <rect x="205" y="32" width="3.5" height="92" fill="#1d1a24"/>
        <rect x="149" y="84" width="17" height="7" rx="1.5" fill="#fff" stroke="#ccc" stroke-width=".4"/><text x="157.5" y="89" font-size="3.6" text-anchor="middle">15 May</text>
        <rect x="198" y="22" width="17" height="7" rx="1.5" fill="#fff" stroke="#ccc" stroke-width=".4"/><text x="206.5" y="27" font-size="3.6" text-anchor="middle">22 May</text>
        <line x1="0" y1="124" x2="440" y2="124" stroke="#9a96ab" stroke-width=".6"/>
        <g font-size="3.6" fill="#6b6780" text-anchor="middle">
          <text x="8" y="133">10 May</text><text x="31" y="133">12:00</text><text x="54" y="133">11 May</text><text x="77" y="133">12:00</text><text x="100" y="133">12 May</text><text x="123" y="133">12:00</text><text x="146" y="133">13 May</text><text x="169" y="133">12:00</text><text x="192" y="133">14 May</text><text x="215" y="133">12:00</text><text x="238" y="133">15 May</text><text x="261" y="133">12:00</text><text x="284" y="133">16 May</text><text x="307" y="133">12:00</text><text x="330" y="133">17 May</text><text x="353" y="133">12:00</text><text x="376" y="133">18 May</text><text x="399" y="133">12:00</text><text x="424" y="133">19 May</text>
        </g>
        <text x="220" y="146" font-size="4.6" font-weight="600" text-anchor="middle" fill="#1d1a24">DATE RANGE</text>
      </svg>
    </section>
    <section class="analysis">
      <h2 class="analysis__title">QuillVane Learning Analysis</h2>
      <p class="analysis__text">Lorem ipsum <b>dolor</b> sit amet, consectetur adipiscing elit. Nam <b>rutrum commodo</b> enim id bibendum. Nunc dignissim risus <b>dolor</b> nec finibus dictum eu. Aliquam sit amet euismod metus, quis malesuada erat. Sed id felis quis nulla feugiat cursus at at <b>dolor</b>. Maecenas pretium aliquet dapibus. Fusce et eleifend massa. Sed convallis ex mi, at lobortis ligula congue vel.</p>
    </section>
  </main>
</section>

<!-- Vocabulary picker screen -->
<section class="screen screen--picker">
  <header class="topbar">
    <span class="brand">QuillVane ▾</span>
    <div class="topbar__tools"><span class="tool"></span><span class="tool"></span><span class="tool"></span><span class="account"></span></div>
  </header>
  <nav class="rail">
    <div class="rail__item rail__item--active"><svg viewBox="0 0 10 10"><path d="M1 5 5 1l4 4v4H6V6H4v3H1z" fill="currentColor"/></svg>QuillVane</div>
    <div class="rail__item"><svg viewBox="0 0 10 10"><path d="M5 1a3 3 0 0 1 3 3c0 2-3 5-3 5S2 6 2 4a3 3 0 0 1 3-3z" fill="currentColor"/></svg>Daily<br>English</div>
    <div class="rail__item"><svg viewBox="0 0 10 10"><path d="M1 9h8V4L5 1 1 4zM3 5h1v3H3zm3 0h1v3H6z" fill="currentColor"/></svg>Business</div>
  </nav>
  <aside class="vocab-nav">
    <div class="vocab-nav__select"><span>All</span><span>▾</span></div>
    <div class="vocab-group">
      <div class="vocab-group__title">Short-Term Memory <span class="info">?</span></div>
      <ul><li class="current">GRAB</li></ul>
    </div>
    <div class="vocab-group">
      <div class="vocab-group__title">Working Memory <span class="info">?</span></div>
      <ul><li>Cool Down</li><li>Cram</li><li>Go For</li><li>Go To</li><li>In The Mood For</li><li>Sip</li><li>Soothing</li><li>Stick With</li><li>Throw In/Throw On</li></ul>
    </div>
    <div class="vocab-group">
      <div class="vocab-group__title">Long-Term Memory <span class="info">?</span></div>
      <ul><li>Give It A Try</li></ul>
    </div>
  </aside>
  <main class="main">
    <div class="reviews">
      <div class="review review--done"><div class="review__label">REVIEW 1</div><div class="review__status">Completed</div><div class="review__bar"><span></span></div><div class="review__mark"><svg viewBox="0 0 10 10"><circle cx="5" cy="5" r="5" fill="#6e56cf"/><path d="M3 5.2 4.4 6.5 7 3.8" stroke="#fff" stroke-width="1.1" fill="none"/></svg></div></div>
      <div class="review review--here"><div class="review__label">REVIEW 2</div><div class="review__status">You are here</div><div class="review__bar"><span></span></div><div class="review__mark"><svg viewBox="0 0 10 10"><circle cx="5" cy="3.4" r="1.8" fill="#e8713c"/><path d="M1.8 9a3.2 3.2 0 0 1 6.4 0z" fill="#e8713c"/></svg></div></div>
      <div class="review review--next"><div class="review__label">REVIEW 3</div><div class="review__status">Unvisited</div><div class="review__mark"></div></div>
      <div class="review review--last"><div class="review__label">REVIEW 4</div><div class="review__status">Unvisited</div><div class="review__mark"></div></div>
    </div>
    <article class="word">
      <h1 class="word__title">Grab</h1>
    </article>
    <div class="exercise">
      <div class="exercise__art" role="img" aria-label="Illustration of a learner studying with a laptop"></div>
      <div class="exercise__cta">START VOCABULARY<br>REVIEW EXERCISE 3</div>
    </div>
    <section class="curve-card">
      <h2 class="curve-card__title">Learning Curve Graph</h2>
      <svg width="440" height="155" viewBox="0 0 440 155" font-family="Poppins, sans-serif">
        <rect x="0" y="3" width="440" height="26" fill="#eeeafb"/>
        <rect x="0" y="29" width="440" height="59" fill="#eaf7ea"/>
        <rect x="0" y="88" width="440" height="16" fill="#fdebe1"/>
        <rect x="0" y="104" width="440" height="20" fill="#e4f2fa"/>
        <g font-size="4.4" fill="#8a86a0"><text x="4" y="96">Short-Term Memory</text><text x="4" y="113">Forgotten Memory</text></g>
        <rect x="156" y="94" width="3.5" height="30" fill="#1d1a24"/>
        <rect x="205" y="32" width="3.5" height="92" fill="#1d1a24"/>
        <rect x="149" y="84" width="17" height="7" rx="1.5" fill="#fff" stroke="#ccc" stroke-width=".4"/><text x="157.5" y="89" font-size="3.6" text-anchor="middle">15 May</text>
        <line x1="0" y1="124" x2="440" y2="124" stroke="#9a96ab" stroke-width=".6"/>
        <g font-size="3.6" fill="#6b6780" text-anchor="middle">
          <text x="8" y="133">10 May</text><text x="31" y="133">12:00</text><text x="54" y="133">11 May</text><text x="77" y="133">12:00</text><text x="100" y="133">12 May</text><text x="123" y="133">12:00</text><text x="146" y="133">13 May</text><text x="169" y="133">12:00</text><text x="192" y="133">14 May</text><text x="215" y="133">12:00</text><text x="238" y="133">15 May</text><text x="261" y="133">12:00</text><text x="284" y="133">16 May</text><text x="307" y="133">12:00</text><text x="330" y="133">17 May</text><text x="353" y="133">12:00</text><text x="376" y="133">18 May</text><text x="399" y="133">12:00</text><text x="424" y="133">19 May</text>
        </g>
        <text x="220" y="146" font-size="4.6" font-weight="600" text-anchor="middle" fill="#1d1a24">DATE RANGE</text>
      </svg>
    </section>
    <section class="analysis">
      <h2 class="analysis__title">QuillVane Learning Analysis</h2>
      <p class="analysis__text">Lorem ipsum <b>dolor</b> sit amet, consectetur adipiscing elit. Nam <b>rutrum commodo</b> enim id bibendum. Nunc dignissim risus <b>dolor</b> nec finibus dictum eu. Aliquam sit amet euismod metus, quis malesuada erat. Sed id felis quis nulla feugiat cursus at at <b>dolor</b>. Maecenas pretium aliquet dapibus. Fusce et eleifend massa. Sed convallis ex mi, at lobortis ligula congue vel.</p>
    </section>
  </main>
  <div class="scrim"></div>
  <div class="picker" role="dialog" aria-label="All vocabulary">
    <div class="picker__select"><span>All</span><span>▾</span></div>
    <span class="picker__close">×</span>
    <div class="picker__group">
      <h3>Short-Term Memory <span class="info">?</span></h3>
      <div class="picker__plain">Grab</div>
    </div>
    <div class="picker__group">
      <h3>Working Memory <span class="info">?</span></h3>
      <div class="picker__words"><span class="chip">Cool Down</span><span class="chip">Cram</span><span class="chip">Go For</span><span class="chip">Go To</span><span class="chip">In The Mood For</span><span class="chip">Sip</span><span class="chip">Soothing</span><span class="chip">Stick With</span><span class="chip">Throw In/Throw On</span></div>
    </div>
    <div class="picker__group">
      <h3>Long-Term Memory <span class="info">?</span></h3>
      <div class="picker__words"><span class="chip">Give It A Try</span></div>
    </div>
  </div>
</section>

</body>
</html>
```